WordPress Design (redesign) and Coding for Funeral Consulting Services & mobile app

I need an attractive SEO friendly WordPress design.

Incorporating all of the latest design standards in a graceful and appealing way. I'd like to see CTA's for for funeral consulting services. People should be able to purchase my consulting services directly from the website so I'd like to see nice buttons.

Funeral Consulting Services are the main topic for this website.

I also have an iOS app called Velomarque in the iOS Appvault Shelf. I want buttons and CTAs so that users can download the app right to their iOS device(s). Make this a secondary focus.

I want more of a mobile focus as that is where I expect the most traffic. Mobile users like to act quickly and they also like to scroll if their interest is captured so I want the design to reflect that.

End to end design
Large Creative Typography for increased mobile searchers.
attractive CTA’s
RGB Vivid / Bright Colors that match our logo
A menu that is easy to find and use on mobile devices
button(s) for iOS app download.

the current website is www.velomarque-example.com This website was a placeholder.
Updates

I'd need users to fill out a survey so that I may collect information from them to better provide service to them.

reference websites: Quillvant.com & Torbex.com for website design inspiratioin. reference Harnwick.com for blog

Target Market(s)

18-35 year old mobile users

Industry/Entity Type

Consulting

Coding

Coded - Design and coding required

Font styles to use
Sans Serif

Colors
fbee3d
000000
ffffff
cbcbcb
fefdec

Requirements
Must have
• iOS app logo and iOS app logo colors should have its own area/page
• CTA's for consulting services and app download. Main topic
• reviews (testimonials)
• Video area
• end to end design
• creative typography
Nice to have
• a beautiful blog page that blends well with the design
Should not have
• Any imagery related to funerals or burials.

```html
<!DOCTYPE html>
<html lang="en">
<head>
<meta charset="utf-8">
<title>Velomarque — Funeral Consulting</title>
<link href="https://fonts.googleapis.com/css2?family=Montserrat:wght@300;400;500;600;700&display=swap" rel="stylesheet">
<style>
:root{
  --yellow:#fbee3d;
  --black:#000000;
  --white:#ffffff;
  --grey:#cbcbcb;
  --cream:#fefdec;
  --ink:#222222;
  --muted:#555555;
  --gold:#d9b44a;
}
*{box-sizing:border-box;margin:0;padding:0}
html,body{width:1200px;height:3838px;overflow:hidden}
body{position:relative;background:var(--white);font-family:'Montserrat',sans-serif;color:var(--ink)}
.abs{position:absolute}
.btn{position:absolute;display:flex;align-items:center;justify-content:center;font-weight:500;font-size:19px;border-radius:2px}
.btn-yellow{background:var(--yellow);color:var(--black)}
.btn-black{background:var(--black);color:var(--yellow);box-shadow:0 3px 6px rgba(0,0,0,.35)}
.center{text-align:center;left:0;width:1200px}

/* header */
.site-header{position:absolute;top:0;left:0;width:1200px;height:113px;background:var(--white);z-index:3}
.brand{position:absolute;left:86px;top:34px;display:flex;align-items:center;gap:12px;font-weight:700;font-size:34px;color:var(--black)}
.brand-dot{width:16px;height:16px;border-radius:50%;background:var(--yellow)}
.main-nav{position:absolute;left:410px;top:46px;display:flex;gap:34px;font-size:15px;font-weight:500;color:var(--black)}
.nav-cta{left:1000px;top:38px;width:112px;height:40px;font-size:14px}

/* hero */
.hero-photo{position:absolute;top:113px;left:0;width:1200px;height:540px;background:linear-gradient(180deg,#5a5d62 0%,#3b3c3f 45%,#2c2b2b 100%)}
.hero-shade{position:absolute;top:113px;left:0;width:1200px;height:540px;background:radial-gradient(ellipse at 50% 55%,rgba(0,0,0,.15),rgba(0,0,0,.45))}
.hero-lead{top:282px;font-size:35px;font-weight:300;color:var(--white);letter-spacing:.5px}
.hero-title{top:330px;font-size:35px;font-weight:700;color:var(--white);line-height:48px;letter-spacing:.5px}
.slider-arrows{position:absolute;top:560px;left:562px;display:flex;gap:8px}
.slider-arrows span{width:30px;height:30px;border-radius:50%;background:var(--white);display:flex;align-items:center;justify-content:center}

/* intro */
.intro-text{top:692px;left:190px;width:820px;text-align:center;font-size:17px;line-height:31px;color:var(--ink)}

/* candle band */
.band-photo{position:absolute;top:934px;left:0;width:1200px;height:338px;background:radial-gradient(ellipse at 30% 80%,#6b4a1c 0%,#2a1d0d 40%,#0c0906 100%)}
.band-text{top:1076px;font-size:18px;line-height:30px;color:var(--yellow);font-weight:500}

/* app */
.app-title{left:86px;top:1383px;font-size:30px;font-weight:700;letter-spacing:1px;color:var(--black)}
.app-text{left:86px;top:1428px;width:520px;font-size:17px;line-height:23px;color:var(--ink)}
.screen{position:absolute;border:1px solid #ddd;box-shadow:0 4px 14px rgba(0,0,0,.2)}
.dots{position:absolute;left:852px;top:1672px;display:flex;gap:4px}
.dots span{width:14px;height:14px;border-radius:50%;border:2px solid var(--black)}
.dots span.on{background:var(--black)}

/* consultant band */
.pattern-band{position:absolute;top:1773px;left:0;width:1200px;height:300px;background:radial-gradient(ellipse at 50% 40%,#2a2a2a 0%,#111 60%,#000 100%)}
.consult-text{top:1822px;left:150px;width:900px;text-align:center;font-size:17.5px;line-height:29px;font-weight:700;color:var(--yellow)}

/* reviews */
.section-title{font-size:30px;font-weight:700;color:var(--black);letter-spacing:1px}
.review-card{position:absolute;top:2172px;width:500px;height:190px;border:2px solid var(--yellow);background:var(--white);text-align:center;padding:20px 36px 0}
.review-card p{font-size:13px;font-style:italic;line-height:22px;color:var(--muted)}
.stars{margin-top:16px;color:var(--gold);font-size:20px;letter-spacing:6px}
.reviewer{margin-top:6px;font-size:17px;font-weight:600;color:var(--black)}
.round-arrow{position:absolute;top:2251px;width:30px;height:30px;border-radius:50%;background:#9a9a9a;display:flex;align-items:center;justify-content:center}

/* video */
.video-bg{position:absolute;top:2443px;left:0;width:1200px;height:468px;background:linear-gradient(90deg,#8c8f94 0%,#c9c6bb 30%,#b7b08d 70%,#8f8a57 100%)}
.video-panel{position:absolute;top:2443px;left:350px;width:417px;height:468px;background:rgba(255,255,255,.35)}
.video-name{top:2458px;left:350px;width:417px;text-align:center;font-size:38px;font-weight:500;color:var(--black)}
.video-sub{top:2508px;left:350px;width:417px;text-align:center;font-size:33px;font-weight:500;color:var(--black)}
.video-frame{position:absolute;top:2571px;left:420px;width:278px;height:166px;background:#1b1b1b;border:5px solid #111;display:flex;align-items:center;justify-content:center}
.video-store{top:2764px;left:350px;width:417px;text-align:center;font-size:37px;line-height:52px;font-weight:500;color:var(--black)}

/* blog */
.blog-card{position:absolute;top:3026px;width:248px;height:345px;background:var(--white);box-shadow:0 1px 5px rgba(0,0,0,.18);text-align:center}
.blog-img{height:160px;width:100%}
.blog-card h3{margin:18px 14px 0;font-size:14.5px;font-weight:500;line-height:21px;color:var(--black)}
.blog-card p{margin:10px 14px 0;font-size:11.5px;line-height:17px;color:var(--muted)}
.blog-card .more{display:block;margin-top:14px;font-size:11.5px;color:var(--muted)}

/* footer */
.site-footer{position:absolute;top:3453px;left:0;width:1200px;height:333px;background:#0a0a0a}
.footer-badge{position:absolute;left:97px;top:3527px;width:200px;height:200px;border-radius:50%;border:10px solid var(--yellow);background:var(--white);display:flex;align-items:center;justify-content:center;font-size:27px;font-weight:700;color:var(--black)}
.footer-head{position:absolute;top:3498px;font-size:18px;font-weight:500;color:var(--white)}
.info-line{position:absolute;left:409px;display:flex;gap:16px;font-size:15px;line-height:22px;color:var(--white)}
.info-line svg{flex:none;margin-top:2px}
.quick-links{position:absolute;left:680px;top:3540px;font-size:14px;line-height:23px;color:var(--white);list-style:none}
.quick-links li::before{content:"›";margin-right:8px}
.social{position:absolute;left:409px;top:3712px;display:flex;gap:14px}
.social span{width:16px;height:16px;border-radius:50%;background:var(--white)}
.email-field{position:absolute;left:842px;top:3548px;width:271px;height:49px;border:2px solid var(--white);color:var(--grey);font-size:13px;padding:15px 20px}
.submit{left:842px;top:3614px;width:194px;height:49px;font-weight:700;font-size:19px}
.copyright{position:absolute;top:3786px;left:0;width:1200px;height:52px;background:var(--yellow);display:flex;align-items:center;justify-content:center;font-size:13px;font-weight:500;color:var(--black)}
</style>
</head>
<body>

<header class="site-header">
  <div class="brand"><span class="brand-dot"></span>Velomarque</div>
  <nav class="main-nav"><span>HOME</span><span>FEATURES</span><span>SCREENSHOT</span><span>REVIEW</span><span>BLOG</span><span>CONTACT US</span></nav>
  <div class="btn btn-black nav-cta">Get App Now</div>
</header>

<div class="hero-photo" role="img" aria-label="Photo of a consultant seated with a couple discussing plans"></div>
<div class="hero-shade"></div>
<div class="abs center hero-lead">THE FIRST STEP IN FUNERAL PLANNING,</div>
<div class="abs center hero-title">PARTICULARLY IF YOU FIND YOURSELF AT-NEED,<br>IS TO GET A FRIEND BY YOUR SIDE.</div>
<div class="btn btn-yellow" style="left:482px;top:433px;width:236px;height:48px">SAVE MONEY TODAY</div>
<svg class="abs" style="left:0;top:500px" width="1200" height="160" viewBox="0 500 1200 160"><path d="M0,520 Q600,700 1200,520 V660 H0 Z" fill="#fff"/></svg>
<div class="slider-arrows">
  <span><svg width="10" height="12" viewBox="0 0 10 12"><path d="M7 1 2 6l5 5" fill="none" stroke="#000" stroke-width="2"/></svg></span>
  <span><svg width="10" height="12" viewBox="0 0 10 12"><path d="M3 1l5 5-5 5" fill="none" stroke="#000" stroke-width="2"/></svg></span>
</div>

<svg class="abs" style="left:520px;top:640px" width="160" height="16" viewBox="0 0 160 16"><line x1="0" y1="8" x2="68" y2="8" stroke="#c9a13b" stroke-width="1.5"/><circle cx="80" cy="8" r="5" fill="none" stroke="#c9a13b" stroke-width="1.5"/><line x1="92" y1="8" x2="160" y2="8" stroke="#c9a13b" stroke-width="1.5"/></svg>
<p class="abs intro-text">Funerals are expensive. Having to finance one suddenly can be a burden to many families, especially those that are uninsured or unprepared. Not coincidently, there is often a windfall of money at this time, in the form of donations, family contributions, and life insurance proceeds. Families tend to consider that money ‘going away’ funds. The funeral industry wants to pressure you into spending your last dollar on that event.</p>

<div class="band-photo" role="img" aria-label="Soft warm background of glowing lights"></div>
<svg class="abs" style="left:0;top:934px" width="1200" height="160" viewBox="0 934 1200 160"><path d="M0,934 Q600,1090 1200,934 Z" fill="#fff"/></svg>
<div class="btn btn-black" style="left:465px;top:883px;width:270px;height:45px;font-size:17px">DON'T Throw Money Away</div>
<div class="abs center band-text">The fact is, life insurance was never intended to be fully used on a fancy funeral, but rather as<br>a hedge against disaster for the survivors.</div>
<div class="btn btn-yellow" style="left:482px;top:1156px;width:236px;height:46px;font-size:18px">SAVE MONEY NOW</div>

<h2 class="abs app-title">GET THE APP</h2>
<p class="abs app-text">Lorem ipsum dolor sit amet consectetur adipisicing elit sed do eiusmod tempor incididunt ut labore et dolore magna aliqua ut enim ad minim veniam quis nostrud.</p>
<div class="btn btn-black" style="left:86px;top:1532px;width:187px;height:40px;font-size:15px">Download Now !</div>
<div class="screen" style="left:703px;top:1380px;width:130px;height:250px;background:linear-gradient(180deg,#222 0 24px,#fff 24px)" role="img" aria-label="App screen with sign-in form"></div>
<div class="screen" style="left:958px;top:1380px;width:137px;height:250px;background:linear-gradient(180deg,#222 0 24px,#fff 24px)" role="img" aria-label="App screen with a profile"></div>
<div class="screen" style="left:805px;top:1356px;width:175px;height:274px;background:linear-gradient(180deg,#f2f2ea 0%,#c7d28f 45%,#7b9a3c 100%)" role="img" aria-label="App welcome screen over a green meadow"></div>
<div class="abs" style="left:805px;top:1445px;width:175px;text-align:center;font-size:22px;font-weight:700;color:#000">Velomarque</div>
<div class="dots"><span></span><span></span><span class="on"></span><span></span><span></span></div>

<div class="pattern-band" role="img" aria-label="Dark patterned background with faint lights"></div>
<svg class="abs" style="left:0;top:1940px" width="1200" height="133" viewBox="0 1940 1200 133"><path d="M0,2073 Q600,1960 1200,2073 Z" fill="#fff"/></svg>
<p class="abs consult-text">A funeral consultant is someone who, on their own, goes out and does all the things related to making funeral arrangements. However we do so with your budget and your ideals in mind. We represent you as your spokesperson and friend during this tough time.</p>
<div class="btn btn-yellow" style="left:482px;top:1936px;width:236px;height:47px;font-size:18px;font-weight:600">Get Help ASAP</div>

<h2 class="abs center section-title" style="top:2100px">VELOMARQUE REVIEWS</h2>
<div class="round-arrow" style="left:26px"><svg width="10" height="12"><path d="M7 1 2 6l5 5" fill="none" stroke="#fff" stroke-width="2"/></svg></div>
<div class="round-arrow" style="left:1144px"><svg width="10" height="12"><path d="M3 1l5 5-5 5" fill="none" stroke="#fff" stroke-width="2"/></svg></div>
<div class="review-card" style="left:92px"><p>"Lorem Ipsum is simply dummy text of the printing and typesetting industry. Lorem Ipsum has been the industry's standard dummy text ever since the 1500s, when an unknown printer took a galley."</p><div class="stars">★★★★★</div><div class="reviewer">Dana L Ortiz</div></div>
<div class="review-card" style="left:609px"><p>"Lorem Ipsum is simply dummy text of the printing and typesetting industry. Lorem Ipsum has been the industry's standard dummy text ever since the 1500s, when an unknown printer took a galley."</p><div class="stars">★★★★★</div><div class="reviewer">Henry P Walsh</div></div>

<div class="video-bg" role="img" aria-label="Blurred soft outdoor background"></div>
<div class="video-panel"></div>
<div class="abs video-name">Velomarque</div>
<div class="abs video-sub">Tribute Your Deceased</div>
<div class="video-frame" role="img" aria-label="App preview video">
  <svg width="120" height="80" viewBox="0 0 120 80"><rect width="120" height="80" rx="16" fill="#29a3f2"/><path d="M48 22v36l30-18z" fill="#fff"/></svg>
</div>
<div class="abs video-store">In The Appvault Shelf<br>Now !</div>

<h2 class="abs center section-title" style="top:2966px">The Blog</h2>
<article class="blog-card" style="left:87px"><div class="blog-img" style="background:linear-gradient(135deg,#3f7d5c,#a9c7a8)" role="img" aria-label="Photo of a smiling young woman"></div><h3>Lorem Ipsum is simply dummy of the typesetting</h3><p>Lorem Ipsum is simply dummy text of the printing and typesetting industry. Lorem dummy text ever since the 1500s</p><span class="more">Read More &gt;</span></article>
<article class="blog-card" style="left:345px"><div class="blog-img" style="background:linear-gradient(135deg,#2a2118,#c99a5a)" role="img" aria-label="Photo of glowing tea lights"></div><h3>Lorem Ipsum is simply dummy of the typesetting</h3><p>Lorem Ipsum is simply dummy text of the printing and typesetting industry. Lorem dummy text ever since the 1500s</p><span class="more">Read More &gt;</span></article>
<article class="blog-card" style="left:606px"><div class="blog-img" style="background:linear-gradient(135deg,#3a3c42,#9da3ab)" role="img" aria-label="Photo of hands signing paperwork"></div><h3>Lorem Ipsum is simply dummy of the typesetting</h3><p>Lorem Ipsum is simply dummy text of the printing and typesetting industry. Lorem dummy text ever since the 1500s</p><span class="more">Read More &gt;</span></article>
<article class="blog-card" style="left:865px"><div class="blog-img" style="background:linear-gradient(135deg,#6f8fb5,#e7b7c8)" role="img" aria-label="Photo of a pink flower on blue water"></div><h3>Lorem Ipsum is simply dummy of the typesetting</h3><p>Lorem Ipsum is simply dummy text of the printing and typesetting industry. Lorem dummy text ever since the 1500s</p><span class="more">Read More &gt;</span></article>

<footer class="site-footer"></footer>
<div class="footer-badge">Velomarque</div>
<div class="footer-head" style="left:409px">More Info:</div>
<div class="info-line" style="top:3540px"><svg width="14" height="18" viewBox="0 0 14 18"><path d="M7 0a7 7 0 0 0-7 7c0 5 7 11 7 11s7-6 7-11a7 7 0 0 0-7-7zm0 10a3 3 0 1 1 0-6 3 3 0 0 1 0 6z" fill="#fff"/></svg><span>Velomarque<br>Elmbrook Vale, NSW 2199</span></div>
<div class="info-line" style="top:3608px"><svg width="16" height="16" viewBox="0 0 16 16"><path d="M3 1l3 3-2 2c1 2 3 4 5 5l2-2 3 3-2 3C6 15 1 10 1 3z" fill="#fff"/></svg><span>0123 456789</span></div>
<div class="info-line" style="top:3651px"><svg width="16" height="12" viewBox="0 0 16 12"><rect width="16" height="12" fill="#fff"/><path d="M0 0l8 7 8-7" fill="none" stroke="#0a0a0a" stroke-width="1.5"/></svg><span>hello@velomarque-example.com</span></div>
<div class="social"><span></span><span></span><span></span><span></span></div>
<div class="footer-head" style="left:680px">Quick Links:</div>
<ul class="quick-links"><li>Home</li><li>Features</li><li>Screenshot</li><li>Review</li><li>Blog</li><li>Contact US</li></ul>
<div class="footer-head" style="left:842px">Newsletter Signup</div>
<div class="email-field">Email Address</div>
<div class="btn btn-yellow submit">SUBMIT</div>
<div class="copyright">Copyright © 2017 Velomarque. All rights reserved.</div>

</body>
</html>
```